WordPress Website Design for Multi-Brand Aviation Group (Unified Branding System)

Project Overview:
We are seeking a professional, modern WordPress website design for an aviation-focused umbrella company that owns and operates multiple subsidiary businesses. The goal is to create a cohesive visual system that clearly communicates that each company operates under the same parent organization, while still allowing each brand to maintain a slightly distinct identity.
This is not just a single website design—we are looking for a scalable design framework that can be applied across multiple aviation-related businesses.
Objectives:
- Establish a consistent, recognizable brand identity across all company websites
Clearly communicate the relationship between the parent company and its subsidiaries
-bCreate a clean, high-end corporate aviation aesthetic
- Ensure all designs are SEO-friendly and optimized for performance
- Allow flexibility for future expansion (additional subsidiaries)
- Target Audience:
- Corporate aviation clients
- Charter customers
- Students wishing to receive flight training
- Aircraft owners and operators
- Turbine aircraft training to meet insurance requirements
- Business professionals and high-net-worth individuals
- Aviation industry partners
Design Direction & Style:
We are looking for a premium, professional aviation feel—think clean, modern, and high-trust. The design should reflect the standards of corporate aviation: precision, safety, and sophistication.
Key style notes:
Minimalist but impactful layout
High-quality aviation photography (jets, interiors, operations, global travel)
Subtle motion/interaction (hover effects, transitions)
Clear typography hierarchy for readability and professionalism
Branding Requirements:
Incorporate the primary colors of the parent company logo across all designs
Website Structure (Core Pages):
Design a system that includes:
Home Page with the following links:
- About / Company Overview
- Aircraft Management
- Aircraft Acquisition
- Charter
- Pilot Services
- Trip Support
- Contact Page
Site should further include:
- Mobile-first responsive design
- Fast-loading, performance-optimized layouts
SEO & Technical Considerations:
- Design should support high-level SEO implementation:
- Clean layout structure that translates well to semantic HTML
- Proper heading hierarchy (H1, H2, H3)
- Space for keyword-rich content without clutter
- Optimized image placement (with alt text capability)
- Fast load times (lightweight design approach)
- Compatibility with WordPress SEO plugins (e.g., Yoast or Rank Math)
WordPress Requirements:
- Design should be easily built using WordPress (preferred builders: Elementor, Gutenberg, or similar)
- Reusable templates for scalability across multiple sites
- Easy for non-developers to update text and images
- Modular components (blocks/sections that can be reused across pages and sites)
- Navigation & UX:
- Simple, intuitive navigation
- Sticky header preferred
Style guide including:
- Colors
- Fonts
- Button styles
- Layout system
- Designs similar to high-end corporate aviation, private jet charter, or luxury service brands are preferred—clean, sharp, and premium without being overly flashy.
What We Want to Avoid:
- Overly busy layouts
- Generic templates with no brand identity
- Outdated or “stock” looking aviation designs
- Poor mobile responsiveness
Additional Notes:
We are building a long-term brand system, not just a one-off website. There is potential for ongoing work as we expand additional subsidiary sites.
We value designers who understand branding consistency across multiple business units and can create a scalable, professional system.
Include the attached main company logo "Vireton Aviation Group" and the "Member PJFO" logo on the main page.

```html
<!DOCTYPE html>
<html lang="en">
<head>
<meta charset="utf-8">
<title>Vireton Aviation Group</title>
<link rel="stylesheet" href="https://fonts.googleapis.com/css2?family=Bebas+Neue&family=Inter:wght@400;500;600;700&display=swap">
<style>
:root{
  --blue:#0b43a0;
  --blue-deep:#06307a;
  --blue-text:#1549b0;
  --ink:#111418;
  --muted:#444a55;
  --ghost:#dfe4ec;
  --white:#ffffff;
  --footer:#050608;
  --mist:#eef0f5;
}
*{box-sizing:border-box;margin:0;padding:0}
html,body{width:1200px;height:4717px;overflow:hidden;background:var(--white)}
body{font-family:"Inter",sans-serif;color:var(--ink);position:relative}
.page{position:relative;width:1200px;height:4717px;overflow:hidden}
.display{font-family:"Bebas Neue",sans-serif;font-weight:400;letter-spacing:.5px}

/* header */
.site-header{position:absolute;top:0;left:0;width:1200px;height:100px;z-index:5}
.brand{position:absolute;left:112px;top:34px;color:var(--white);font-family:"Bebas Neue",sans-serif;font-size:34px;line-height:1;letter-spacing:1px}
.nav{position:absolute;left:426px;top:30px;display:flex;align-items:center}
.nav a{font-size:12px;color:var(--white);text-decoration:none;padding:11px 14px;border-radius:4px}
.nav a.active{background:var(--blue);font-weight:600}
.btn-contact{position:absolute;left:998px;top:30px;background:var(--white);color:var(--ink);font-size:12px;font-weight:600;padding:11px 13px;border-radius:4px;text-decoration:none}

/* hero */
.hero-photo{position:absolute;top:0;left:0;width:1200px;height:820px;
  background:linear-gradient(180deg,#1d4ea8 0%,#3f6fb8 30%,#6f86a6 55%,#b08a6e 75%,#2a2f3c 100%);
  clip-path:polygon(0 0,100% 0,100% 660px,50% 800px,0 660px)}
.hero-photo::after{content:"";position:absolute;inset:0;background:linear-gradient(90deg,rgba(12,45,110,.75) 0%,rgba(12,45,110,.2) 55%,rgba(0,0,0,0) 100%)}
.hero-band{position:absolute;top:0;left:0}
.hero-title{position:absolute;left:112px;top:232px;color:var(--white);font-size:58px;line-height:76px;z-index:2}
.hero-text{position:absolute;left:112px;top:464px;width:420px;color:var(--white);font-size:11.5px;line-height:23px;z-index:2}
.btn-white{position:absolute;left:112px;top:561px;background:var(--white);color:var(--ink);font-size:12px;font-weight:600;padding:11px 10px;border-radius:4px;z-index:2}
.dots{position:absolute;left:578px;top:720px;display:flex;gap:6px;z-index:2}
.dots i{width:9px;height:9px;border-radius:50%;background:var(--white);display:block}

/* section heads */
.sec-head{position:absolute;left:0;width:1200px;height:110px;text-align:center}
.sec-head .ghost{position:absolute;left:0;right:0;top:0;font-size:66px;line-height:1;color:var(--ghost)}
.sec-head h2{position:absolute;left:0;right:0;top:42px;font-size:50px;line-height:1;font-weight:400;text-align:center;white-space:nowrap}
.sec-head h2 span{color:var(--blue-text)}
.plane{width:70px;height:30px;display:inline-block;vertical-align:-3px;margin-right:10px}

/* services */
.card{position:absolute;top:1039px;width:310px;height:452px;border-radius:140px;overflow:hidden}
.card .photo{position:absolute;inset:0}
.card .label{position:absolute;left:0;right:0;bottom:34px;text-align:center;color:var(--white);font-weight:700;font-size:18px}
.card .shade{position:absolute;left:0;right:0;bottom:0;height:140px;background:linear-gradient(180deg,rgba(0,0,0,0),rgba(0,0,0,.55))}
.card .overlay{position:absolute;left:10px;right:10px;bottom:0;height:148px;background:var(--blue);border-radius:150px 150px 0 0;color:var(--white);text-align:center}
.card .overlay .ico{position:absolute;left:50%;top:-14px;margin-left:-22px;width:44px;height:44px;border-radius:50%;background:var(--white);display:flex;align-items:center;justify-content:center}
.card .overlay h3{font-size:18px;font-weight:700;margin-top:44px}
.card .overlay p{font-size:11.5px;line-height:18px;margin:8px auto 0;width:230px}
.arrow{position:absolute;width:20px;height:20px;border-radius:50%;display:flex;align-items:center;justify-content:center}

/* why */
.why-photo{position:absolute;left:0;top:1583px;width:557px;height:544px;background:linear-gradient(180deg,#243c68 0%,#5b6f8f 45%,#c08a55 72%,#2c2a2d 100%)}
.why-panel{position:absolute;left:557px;top:1583px;width:643px;height:544px;background:var(--blue)}
.why-ghost{position:absolute;left:80px;top:52px;font-size:62px;color:rgba(255,255,255,.22);line-height:1}
.why-title{position:absolute;left:80px;top:86px;font-size:50px;color:var(--white);font-weight:400;line-height:1;white-space:nowrap}
.feature{position:absolute;left:84px;color:var(--white)}
.feature .row{display:flex;align-items:center;gap:14px}
.feature .badge{width:54px;height:54px;border-radius:50%;background:var(--white);display:flex;align-items:center;justify-content:center}
.feature h3{font-size:21px;font-weight:700}
.feature p{font-size:12.5px;margin-top:10px;margin-left:8px}

/* about */
.about-text{position:absolute;left:230px;top:2344px;width:740px;text-align:center;font-size:13.5px;line-height:26px;color:var(--muted)}
.btn-blue{position:absolute;background:var(--blue);color:var(--white);font-size:12px;font-weight:600;padding:12px 12px;border-radius:4px}

/* serve */
.serve{position:absolute;left:0;top:2578px;width:1200px;height:542px;background:linear-gradient(90deg,#eef0f6 0%,#e8ebf2 45%,#d9dde6 100%)}
.serve-photo{position:absolute;right:0;top:0;width:640px;height:542px;background:linear-gradient(180deg,#e9ecf2 0%,#c9ced8 40%,#5b6677 62%,#9aa2af 80%,#cfd3da 100%);mask-image:linear-gradient(90deg,transparent 0,#000 30%)}
.serve-ghost{position:absolute;left:100px;top:40px;font-size:60px;color:var(--ghost);line-height:1}
.serve-title{position:absolute;left:112px;top:56px;font-size:50px;font-weight:400;line-height:1;white-space:nowrap}
.serve-title span{color:var(--blue-text)}
.serve-list{position:absolute;left:112px;top:136px;list-style:none}
.serve-list li{display:flex;align-items:center;gap:24px;height:54.2px;font-size:20px;color:#333a45}
.serve-list .dot{width:46px;height:46px;border-radius:50%;background:var(--blue);display:flex;align-items:center;justify-content:center}

/* gallery */
.slide{position:absolute;border-radius:12px;overflow:hidden}
.slide-label{position:absolute;left:0;right:0;bottom:22px;text-align:center;color:var(--white);font-size:46px;line-height:1}

/* cta */
.cta-text{position:absolute;left:0;width:1200px;top:4003px;text-align:center;font-size:15px;color:#333a45}
.btn-outline{position:absolute;background:var(--white);color:var(--ink);font-size:12px;font-weight:600;padding:11px 10px;border-radius:4px;border:1.5px solid var(--blue)}

/* footer */
.footer-bg{position:absolute;left:0;top:0}
.foot-h{position:absolute;font-size:21px;color:var(--blue-text);font-weight:500;text-transform:uppercase}
.foot-links{position:absolute;left:114px;top:4438px;list-style:none}
.foot-links li{font-size:12.5px;color:var(--white);height:25.7px}
.foot-brand{position:absolute;left:0;width:1200px;top:4362px;text-align:center;font-family:"Bebas Neue",sans-serif;font-size:60px;line-height:1;color:#1e5cd0;letter-spacing:2px}
.socials{position:absolute;left:512px;top:4492px;display:flex;gap:6px}
.socials i{display:block;width:30px;height:30px;border-radius:50%;background:var(--white)}
.member-of{position:absolute;left:0;width:1200px;top:4562px;text-align:center;color:var(--white);font-size:17px}
.member{position:absolute;left:0;width:1200px;top:4590px;text-align:center;font-family:"Bebas Neue",sans-serif;font-size:58px;line-height:1;color:var(--white);letter-spacing:6px}
.contact-row{position:absolute;left:838px;display:flex;align-items:center;gap:14px;color:var(--white);font-size:13.5px}
.contact-row svg{flex:none}
.foot-line{position:absolute;left:112px;top:4664px;width:980px;height:1px;background:#5a5f68}
.copyright{position:absolute;left:0;width:1200px;top:4685px;text-align:center;color:var(--white);font-size:12.5px}
</style>
</head>
<body>
<div class="page">

<svg width="0" height="0" style="position:absolute">
  <defs>
    <symbol id="plane" viewBox="0 0 70 30"><path d="M2 24 L20 18 L10 10 L16 9 L30 15 L52 8 C60 5 68 5 68 8 C68 11 60 13 52 15 L34 20 L28 29 L23 29 L25 21 L8 26 Z" fill="currentColor"/></symbol>
  </defs>
</svg>

<!-- HERO -->
<div class="hero-photo" role="img" aria-label="Private jet parked on the apron at sunset"></div>
<svg class="hero-band" width="1200" height="830" viewBox="0 0 1200 830">
  <polygon points="0,660 600,800 1200,660 1200,676 600,818 0,676" fill="#0b43a0"/>
</svg>

<header class="site-header">
  <div class="brand">Vireton Aviation Group</div>
  <nav class="nav">
    <a class="active">Home</a><a>About</a><a>Aircraft Management</a><a>Aircraft Acquisition</a><a>Charter</a>
  </nav>
  <a class="btn-contact">Contact Us</a>
</header>

<h1 class="hero-title display">Elevating Aviation<br>Ownership, Charter<br>&amp; Flight Solutions</h1>
<p class="hero-text">Vireton Aviation Group delivers premium aviation services through a network of trusted subsidiaries specializing in aircraft management, charter, acquisitions, pilot services, and trip support.</p>
<div class="btn-white">Explore Services</div>
<div class="dots"><i></i><i></i><i></i></div>

<!-- SERVICES -->
<div class="sec-head" style="top:894px">
  <div class="ghost display">Our Aviation Companies &amp; Services</div>
  <h2 class="display"><svg class="plane"><use href="#plane"/></svg>Our Aviation <span>Companies &amp; Services</span></h2>
</div>

<div class="arrow" style="left:34px;top:1258px;background:var(--blue)"><svg width="10" height="10" viewBox="0 0 10 10"><path d="M6.5 1.5 L3 5 L6.5 8.5" stroke="#fff" stroke-width="1.6" fill="none"/></svg></div>
<div class="arrow" style="left:1142px;top:1260px;background:#e3e5ea"><svg width="10" height="10" viewBox="0 0 10 10"><path d="M3.5 1.5 L7 5 L3.5 8.5" stroke="#fff" stroke-width="1.6" fill="none"/></svg></div>

<div class="card" style="left:114px">
  <div class="photo" role="img" aria-label="Technician servicing a jet in a maintenance hangar" style="background:linear-gradient(180deg,#6e7078 0%,#8a7a62 45%,#b9752f 70%,#3b3b3f 100%)"></div>
  <div class="shade"></div>
  <div class="label">Aircraft&nbsp; Management</div>
</div>
<div class="card" style="left:445px">
  <div class="photo" role="img" aria-label="Flight crew member with headset holding a clipboard" style="background:linear-gradient(180deg,#c9ccd2 0%,#b4b6bb 40%,#294a8e 70%,#203a73 100%)"></div>
  <div class="overlay">
    <div class="ico"><svg width="26" height="26" viewBox="0 0 26 26"><circle cx="13" cy="13" r="11" fill="none" stroke="#0b43a0" stroke-width="2"/><path d="M13 5 L13 21 M6 13 L20 13 M9 19 L17 19" stroke="#0b43a0" stroke-width="2"/></svg></div>
    <h3>Charter Services</h3>
    <p>Private charter solutions tailored for business and leisure travel.</p>
  </div>
</div>
<div class="card" style="left:777px">
  <div class="photo" role="img" aria-label="Passenger using a phone inside a private jet cabin" style="background:linear-gradient(180deg,#8a8b86 0%,#c9b997 35%,#a07a5e 65%,#e6e4e0 100%)"></div>
  <div class="shade"></div>
  <div class="label">Trip Support</div>
</div>

<!-- WHY -->
<div class="why-photo" role="img" aria-label="Passengers boarding a private jet at dusk"></div>
<section class="why-panel">
  <div class="why-ghost display">Why Choose Vireton</div>
  <h2 class="why-title display"><svg class="plane" style="color:#fff"><use href="#plane"/></svg>Why Choose Vireton</h2>
  <div class="feature" style="top:168px">
    <div class="row"><span class="badge"><svg width="26" height="26" viewBox="0 0 26 26"><path d="M13 2 L22 6 V13 C22 19 17 23 13 24 C9 23 4 19 4 13 V6 Z" fill="#0b43a0"/><path d="M9 13 L12 16 L17 10" stroke="#fff" stroke-width="2" fill="none"/></svg></span><h3>Safety First</h3></div>
    <p>Commitment to operational discipline and industry best practices.</p>
  </div>
  <div class="feature" style="top:282px">
    <div class="row"><span class="badge"><svg width="28" height="28" viewBox="0 0 28 28"><path d="M4 11 L9 4 H19 L24 11 L14 24 Z" fill="#0b43a0"/><path d="M4 11 H24 M14 24 L10 11 L14 4 L18 11 Z" stroke="#fff" stroke-width="1.2" fill="none"/></svg></span><h3>Premium Service</h3></div>
    <p>White-glove client experience from inquiry to arrival.</p>
  </div>
  <div class="feature" style="top:394px">
    <div class="row"><span class="badge"><svg width="28" height="28" viewBox="0 0 28 28"><circle cx="14" cy="14" r="10" fill="none" stroke="#0b43a0" stroke-width="4" stroke-dasharray="4 3"/><circle cx="14" cy="14" r="5" fill="#0b43a0"/></svg></span><h3>Industry Expertise</h3></div>
    <p>Experienced leadership across aviation sectors.</p>
  </div>
</section>

<!-- ABOUT -->
<div class="sec-head" style="top:2220px">
  <div class="ghost display">One Aviation Group. Multiple Specialized Solutions.</div>
  <h2 class="display"><svg class="plane"><use href="#plane"/></svg>One Aviation Group. <span>Multiple Specialized Solutions.</span></h2>
</div>
<p class="about-text">Vireton Aviation Group is a modern aviation holding company built to serve aircraft owners, charter clients, flight students, and aviation professionals through a unified network of specialized businesses.We combine operational excellence, safety, and premium service standards across every division</p>
<div class="btn-blue" style="left:554px;top:2447px">Read More</div>

<!-- WHO WE SERVE -->
<section class="serve">
  <div class="serve-photo" role="img" aria-label="Executives greeting beside a helicopter on a helipad"></div>
  <div class="serve-ghost display">Who We Serve</div>
  <h2 class="serve-title display"><svg class="plane"><use href="#plane"/></svg>Who <span>We Serve</span></h2>
  <ul class="serve-list">
    <li><span class="dot"><svg width="20" height="20" viewBox="0 0 20 20"><circle cx="10" cy="6" r="4" fill="#fff"/><path d="M3 19 C3 13 17 13 17 19 Z" fill="#fff"/></svg></span>Aircraft Owners</li>
    <li><span class="dot"><svg width="20" height="20" viewBox="0 0 20 20"><path d="M10 2 V18 M3 10 H17 M6 16 H14" stroke="#fff" stroke-width="2.2"/></svg></span>Charter Travelers</li>
    <li><span class="dot"><svg width="20" height="20" viewBox="0 0 20 20"><rect x="2" y="6" width="16" height="11" rx="2" fill="#fff"/><rect x="7" y="3" width="6" height="4" fill="none" stroke="#fff" stroke-width="1.6"/></svg></span>Corporate Executives</li>
    <li><span class="dot"><svg width="20" height="20" viewBox="0 0 20 20"><circle cx="10" cy="9" r="6" fill="#fff"/><rect x="3" y="15" width="14" height="3" fill="#fff"/></svg></span>High-Net-Worth Individuals</li>
    <li><span class="dot"><svg width="20" height="20" viewBox="0 0 20 20"><path d="M2 7 L10 3 L18 7 L10 11 Z" fill="#fff"/><circle cx="10" cy="13" r="4" fill="#fff"/></svg></span>Flight Students</li>
    <li><span class="dot"><svg width="20" height="20" viewBox="0 0 20 20"><circle cx="9" cy="6" r="4" fill="#fff"/><path d="M2 19 C2 13 14 13 14 19 Z" fill="#fff"/><circle cx="15" cy="14" r="3" fill="#fff"/></svg></span>Insurance Training Clients</li>
    <li><span class="dot"><svg width="20" height="20" viewBox="0 0 20 20"><path d="M2 10 L7 5 L10 8 L13 5 L18 10 L10 17 Z" fill="#fff"/></svg></span>Aviation Partners</li>
  </ul>
</section>

<!-- CORPORATE -->
<div class="sec-head" style="top:3209px">
  <div class="ghost display">Corporate Aviation Without Compromise</div>
  <h2 class="display"><svg class="plane"><use href="#plane"/></svg>Corporate <span>Aviation Without Compromise</span></h2>
</div>
<div class="slide" role="img" aria-label="Jet silhouette against an evening sky" style="left:112px;top:3353px;width:90px;height:426px;background:linear-gradient(180deg,#3a4a66 0%,#8b7a74 50%,#d38a4a 65%,#1c1d22 100%)"></div>
<div class="slide" role="img" aria-label="Private jet cabin with leather seats and a dining table" style="left:227px;top:3349px;width:762px;height:430px;background:linear-gradient(180deg,#d9cfc4 0%,#b07a4c 40%,#8a5634 60%,#3b4f86 85%,#183f96 100%)">
  <div class="slide-label display">Cabins</div>
</div>
<div class="slide" role="img" aria-label="Ground technician walking beside an aircraft" style="left:1000px;top:3353px;width:92px;height:426px;background:linear-gradient(180deg,#e3e5e8 0%,#c9ccd1 40%,#a5483d 60%,#6b6e76 100%)"></div>

<!-- CTA -->
<div class="sec-head" style="top:3878px">
  <div class="ghost display">Ready To Elevate Your Aviation Experience?</div>
  <h2 class="display"><svg class="plane"><use href="#plane"/></svg>Ready To Elevate <span>Your Aviation Experience?</span></h2>
</div>
<p class="cta-text">Speak with our team about ownership, charter, management, or training solutions.</p>
<div class="btn-blue" style="left:472px;top:4057px">Contact Us</div>
<div class="btn-outline" style="left:567px;top:4057px">Schedule Consultation</div>

<!-- FOOTER -->
<svg class="footer-bg" width="1200" height="4717" viewBox="0 0 1200 4717">
  <polygon points="0,4330 600,4195 1200,4330 1200,4717 0,4717" fill="#0b43a0"/>
  <polygon points="0,4346 600,4213 1200,4346 1200,4717 0,4717" fill="#050608"/>
</svg>

<div class="foot-h" style="left:112px;top:4399px">Quick Links</div>
<ul class="foot-links">
  <li>Home</li><li>About</li><li>Aircraft Management</li><li>Aircraft Acquisition</li><li>Charter</li><li>Trip Support</li><li>Contact</li>
</ul>

<div class="foot-brand">Vireton<br><span style="font-size:34px;letter-spacing:5px">Aviation Group</span></div>
<div class="socials" aria-label="Social links"><i></i><i></i><i></i><i></i><i></i></div>
<div class="member-of">member of</div>
<div class="member">PJFO</div>

<div class="foot-h" style="left:838px;top:4401px">Contact Info</div>
<div class="contact-row" style="top:4448px"><svg width="20" height="22" viewBox="0 0 20 22"><path d="M10 1 C5 1 2 5 2 9 C2 14 10 21 10 21 C10 21 18 14 18 9 C18 5 15 1 10 1 Z" fill="#fff"/><circle cx="10" cy="9" r="3" fill="#050608"/></svg>Lorem Ipsum,USA -437916</div>
<div class="contact-row" style="top:4520px"><svg width="20" height="20" viewBox="0 0 20 20"><circle cx="10" cy="10" r="10" fill="#fff"/><path d="M6 5 L8 5 L9 8 L8 9 C8.5 10.5 9.5 11.5 11 12 L12 11 L15 12 L15 14 C15 15 14 15 13 15 C9 14 6 11 5 7 C5 6 5 5 6 5 Z" fill="#050608"/></svg>+1 888 888 8888</div>
<div class="contact-row" style="top:4574px"><svg width="20" height="20" viewBox="0 0 20 20"><circle cx="10" cy="10" r="10" fill="#fff"/><rect x="5" y="6.5" width="10" height="7" rx="1" fill="#050608"/><path d="M5.5 7 L10 10.5 L14.5 7" stroke="#fff" stroke-width="1" fill="none"/></svg>info@viretonaviationgroup.com</div>

<div class="foot-line"></div>
<div class="copyright">© 2026 Vireton Aviation Group.All rights reserved</div>

</div>
</body>
</html>
```